Corvane Paintless Dent Removal

Our company works on vehicles removing dents using a highly skilled trade which the metal is massaged out with special tools without disturbing the original paint, hence paintless dent removal. Besides keeping the paint and metal original its also very environmentally friendly since no paint or toxic fillers are used. Also we we are one of the most experienced companies in the business with 25 years

Target Market(s)

Retail Automobile consumers, Auto Dealerships and Auto Body Shops

Industry/Entity Type

Auto Repair

Contact Information for Business Card

Dale Hollister
PO Box 518 Brookmere, NY 11962
631-555-0148
corvanepdr@mailbox-example.com
website corvanepdr.example
youtube corvane paintless dent removal
25 years of experience removing Dents, Dings and Hail Damage

Font styles to use
Serif
Sans Serif

Colors

Designer to choose colors to be used in the design.

Requirements
Must have
• I do like things that are simple but classy and somewhat bold, also I like my logo so that should be somewhat important

```html
<!DOCTYPE html>
<html lang="en">
<head>
<meta charset="utf-8">
<title>Corvane Paintless Dent Removal – Business Card</title>
<link rel="stylesheet" href="https://fonts.googleapis.com/css2?family=Roboto+Condensed:wght@400;700&display=swap">
<style>
  :root {
    --green: #7cc414;
    --navy: #1f3461;
    --white: #ffffff;
    --paper: #f7f7f5;
    --ink: #4a4f5a;
    --rule: #c9ccd2;
    --stage: #e6e4df;
  }
  * { margin: 0; padding: 0; box-sizing: border-box; }
  html, body { width: 1200px; height: 911px; overflow: hidden; }
  body {
    background: var(--stage);
    font-family: "Roboto Condensed", Arial, sans-serif;
    display: flex;
    align-items: center;
    justify-content: center;
    gap: 40px;
  }
  .card {
    position: relative;
    width: 540px;
    height: 309px;
    overflow: hidden;
    box-shadow: 0 6px 18px rgba(0,0,0,.18);
  }

  /* Front side */
  .card-front { background: var(--paper); }
  .front-wordmark {
    position: absolute;
    left: 34px; top: 96px;
    width: 200px;
    display: flex; align-items: center; gap: 10px;
    color: var(--navy);
    font-weight: 700;
    font-size: 22px;
    line-height: 1.1;
    text-transform: uppercase;
  }
  .front-wordmark .mark-dot {
    flex: none;
    width: 18px; height: 18px;
    border-radius: 50%;
    background: var(--green);
  }
  .front-divider {
    position: absolute;
    left: 252px; top: 70px;
    width: 1px; height: 150px;
    background: var(--rule);
  }
  .experience-seal {
    position: absolute;
    right: 22px; top: 18px;
    width: 46px; height: 46px;
    border-radius: 50%;
    background: var(--navy);
    border: 3px solid #c79a3a;
  }
  .contact {
    position: absolute;
    left: 272px; top: 74px;
    color: var(--ink);
    font-size: 14px;
    line-height: 1.45;
  }
  .contact-name {
    color: var(--navy);
    font-weight: 700;
    font-size: 21px;
    letter-spacing: .5px;
    text-transform: uppercase;
    margin-bottom: 6px;
  }
  .contact-address { margin-bottom: 8px; }
  .contact-line { display: flex; align-items: center; gap: 8px; }
  .contact-line svg { flex: none; width: 13px; height: 13px; }

  .front-footer {
    position: absolute;
    left: 0; right: 0; bottom: 0;
    height: 30px;
  }
  .footer-band {
    position: absolute;
    left: 0; bottom: 0;
    width: 250px; height: 30px;
    background: var(--navy);
    color: var(--white);
    font-size: 13px;
    letter-spacing: 3px;
    display: flex; align-items: center;
    padding-left: 16px;
  }
  .footer-stripes {
    position: absolute;
    left: 250px; right: 0; bottom: 0;
    height: 30px;
    display: flex; flex-direction: column; justify-content: flex-end; gap: 4px;
  }
  .footer-stripes span { display: block; height: 3px; background: var(--green); }
  .footer-stripes span:last-child { height: 10px; }

  /* Back side */
  .card-back { background: var(--green); }
  .back-wordmark {
    position: absolute;
    left: 30px; top: 34px;
    color: var(--white);
    font-weight: 700;
    font-size: 30px;
    line-height: 1.05;
    text-transform: uppercase;
  }
  .back-web {
    position: absolute;
    left: 30px; top: 112px;
    color: var(--white);
    font-size: 14px;
    letter-spacing: 3px;
  }
</style>
</head>
<body>

  <section class="card card-front" aria-label="Card front">
    <div class="front-wordmark"><span class="mark-dot"></span><span>Corvane Paintless Dent Removal</span></div>
    <div class="front-divider"></div>
    <div class="experience-seal" role="img" aria-label="25 years of experience seal"></div>

    <div class="contact">
      <p class="contact-name">Dale Hollister</p>
      <p class="contact-address">PO Box 518<br>Brookmere, NY 11962</p>
      <p class="contact-line">
        <svg viewBox="0 0 16 16" aria-hidden="true"><path fill="#1f3461" d="M3.6 1.5 6 4 4.7 5.8c.9 2 2.5 3.6 4.5 4.5L11 9l2.5 2.4-1.4 2.3C6.6 13.5 2.5 9.4 2.3 3.9z"/></svg>
        <span>631-555-0148</span>
      </p>
      <p class="contact-line">
        <svg viewBox="0 0 16 16" aria-hidden="true"><rect x="1" y="3" width="14" height="10" fill="#1f3461"/><path d="M1.5 3.5 8 9l6.5-5.5" stroke="#fff" stroke-width="1.3" fill="none"/></svg>
        <span>corvanepdr@mailbox-example.com</span>
      </p>
      <p class="contact-line">
        <svg viewBox="0 0 16 16" aria-hidden="true"><rect x="2" y="2" width="12" height="12" fill="#1f3461"/></svg>
        <span>corvane paintless dent removal</span>
      </p>
    </div>

    <div class="front-footer">
      <div class="footer-band">www.corvanepdr.example</div>
      <div class="footer-stripes"><span></span><span></span><span></span></div>
    </div>
  </section>

  <section class="card card-back" aria-label="Card back">
    <p class="back-wordmark">Corvane<br>Paintless Dent Removal</p>
    <p class="back-web">corvanepdr.example</p>
  </section>

</body>
</html>
```